Velvet Lantern rebranding my business with a new business card

I have my new logo and now I need a refresher on my business cards. I really want something fun and fresh. I like black background or anything to make the color pop.
Logo
Name: Velvet Lantern
Contact Info as stated below:
Mira Pellow
555-013-4762
Logo
Name: Velvet Lantern
Mira Pellow
555-013-4762
fb.me/VelvetLanternbyMira
Instagram: @VelvetLanternbyMira

Industry/Entity Type

Business

Contact Information for Business Card

double-sided. Logo on one side. Contact info on the other.

Requirements
Must have
• Logo
• Name: Velvet Lantern
• Contact Info as stated below:
• Mira Pellow
• 555-013-4762
• fb.me/VelvetLanternbyMira
• fb.me/VelvetLanternbyMira

```html
<!DOCTYPE html>
<html lang="en">
<head>
<meta charset="utf-8">
<title>Velvet Lantern – Business Card</title>
<link rel="stylesheet" href="https://fonts.googleapis.com/css2?family=Oswald:wght@500&family=Work+Sans:wght@400;500&display=swap">
<style>
  :root {
    --backdrop: #161616;
    --card: #232323;
    --card-edge: #2c2c2c;
    --teal: #3fc7b3;
    --pink: #e9a3c4;
    --ink-light: #f2f2f2;
    --foil: #a8a8a8;
  }
  * { margin: 0; padding: 0; box-sizing: border-box; }
  html, body {
    width: 1200px; height: 900px; overflow: hidden;
    background: var(--backdrop);
  }
  .canvas {
    position: relative; width: 1200px; height: 900px;
    display: flex; flex-direction: column; align-items: center;
    justify-content: center; gap: 52px;
  }
  .card {
    position: relative; width: 620px; height: 354px;
    background: var(--card);
    border: 1px solid var(--card-edge);
    box-shadow: 0 12px 30px rgba(0,0,0,.55);
  }
  /* Front: logo side */
  .card--front { display: flex; align-items: center; justify-content: center; }
  .brand-mark { display: flex; align-items: center; gap: 12px; margin-top: -18px; }
  .brand-mark__dot {
    width: 22px; height: 22px; border-radius: 50%;
    border: 2px solid var(--foil);
  }
  .brand-mark__name {
    font-family: "Work Sans", sans-serif; font-weight: 500;
    font-size: 26px; letter-spacing: 2px; text-transform: uppercase;
    color: var(--foil);
  }
  /* Back: contact side */
  .card--back { display: flex; align-items: center; justify-content: center; padding-top: 20px; }
  .contact-block { display: flex; align-items: center; gap: 22px; }
  .identity { text-align: right; }
  .identity__name {
    font-family: "Oswald", sans-serif; font-weight: 500;
    font-size: 36px; line-height: 1; letter-spacing: 1px;
    text-transform: uppercase; color: var(--teal);
  }
  .identity__role {
    margin-top: 6px;
    font-family: "Work Sans", sans-serif; font-size: 15px;
    color: var(--ink-light);
  }
  .divider { width: 2px; height: 60px; background: var(--pink); }
  .contact-list { list-style: none; display: flex; flex-direction: column; gap: 6px; }
  .contact-list__item {
    display: flex; align-items: center; gap: 12px;
    font-family: "Work Sans", sans-serif; font-size: 15px;
    letter-spacing: .5px; color: var(--ink-light);
  }
  .contact-list__icon { width: 14px; height: 14px; flex: none; }
</style>
</head>
<body>
<main class="canvas">
  <section class="card card--front" aria-label="Card front">
    <div class="brand-mark">
      <span class="brand-mark__dot"></span>
      <span class="brand-mark__name">Velvet Lantern</span>
    </div>
  </section>

  <section class="card card--back" aria-label="Card back">
    <div class="contact-block">
      <div class="identity">
        <h1 class="identity__name">Mira Pellow</h1>
        <p class="identity__role">Owner</p>
      </div>
      <span class="divider"></span>
      <ul class="contact-list">
        <li class="contact-list__item">
          <svg class="contact-list__icon" viewBox="0 0 14 14" aria-hidden="true">
            <rect x="3.5" y="1" width="7" height="12" rx="1.2" fill="none" stroke="var(--teal)" stroke-width="1.3"/>
            <line x1="6" y1="11" x2="8" y2="11" stroke="var(--teal)" stroke-width="1.2"/>
          </svg>
          555-013-4762
        </li>
        <li class="contact-list__item">
          <svg class="contact-list__icon" viewBox="0 0 14 14" aria-hidden="true">
            <rect x="1" y="3" width="12" height="8.5" fill="var(--teal)"/>
            <polyline points="1,3 7,8 13,3" fill="none" stroke="var(--card)" stroke-width="1.2"/>
          </svg>
          info@mirapellow.com
        </li>
        <li class="contact-list__item">
          <svg class="contact-list__icon" viewBox="0 0 14 14" aria-hidden="true">
            <rect x="1.5" y="1.5" width="11" height="11" rx="2" fill="var(--teal)"/>
          </svg>
          fb.me/VelvetLanternbyMira
        </li>
      </ul>
    </div>
  </section>
</main>
</body>
</html>
```